Healthy lifestyle Influencer business card

I need your creativity to have a business card that I can leave in all the restaurants, hotels and spas I visit to inform them that I am an influencer specializing in the wellness sector and that I will write a review about them. You can use my instagram photos Lunavita27 or on my website www.piattileggeriorto.it. I would like my business card to impress with its creativity! thank you very much!

Contact Information for Business Card

siteweb, instagram, phone number

Font styles to use
Decorative
Script

Colors
0094D4
00A9DD
6FCCEA
C7EBF8
E9F6FB
59FF00
82FF00
B8FF75
E3FFCB
F4FFEA
FFC000
F8CF3A
FAE287
FDF2CF
FEFAEE
F0912C
F2A743
F7CA91
FBE8D2
FDF5EE
EE7325
F08F49
F5BC92
FAE3D3
FDF4ED
EB3D1F
EC4F4E
F09395
F8D3D4
FCEDEE
E54698
E96AAD
F1A4CE
F9D9EA
FCEFF6

Requirements
Nice to have
• creativity

```html
<!DOCTYPE html>
<html lang="it">
<head>
<meta charset="utf-8">
<title>Lunavita Chef – Biglietto da visita</title>
<link rel="stylesheet" href="https://fonts.googleapis.com/css2?family=Great+Vibes&family=Nunito:wght@600&family=Roboto:wght@300&display=swap">
<style>
  :root {
    --page-bg: #e7e3de;
    --card-top: #f4f2ef;
    --card-bottom: #e6e3df;
    --ink: #3a3a3a;
    --ink-soft: #4f4f4f;
    --contact-ink: #5a5a5a;
    --icon-ink: #8a9a94;
    --band-dark: #3b3936;
    --band-text: #c9c6c1;
    --strip-teal: #9fc9c3;
    --dot-pink: #e96aad;
  }
  * { margin: 0; padding: 0; box-sizing: border-box; }
  html, body { width: 1200px; height: 1054px; overflow: hidden; }
  body {
    background: var(--page-bg);
    position: relative;
    font-family: "Roboto", sans-serif;
  }
  .business-card {
    position: absolute;
    left: 100px;
    top: 227px;
    width: 1000px;
    height: 600px;
    border-radius: 24px;
    overflow: hidden;
    background: linear-gradient(160deg, var(--card-top), var(--card-bottom));
    box-shadow: 0 14px 40px rgba(0,0,0,0.12);
  }
  .brand-name {
    position: absolute;
    left: 38px;
    top: 104px;
    font-family: "Great Vibes", cursive;
    font-size: 92px;
    color: var(--ink);
    line-height: 1;
    white-space: nowrap;
  }
  .tagline {
    position: absolute;
    left: 118px;
    top: 214px;
    font-family: "Nunito", sans-serif;
    font-weight: 600;
    font-size: 28px;
    color: var(--ink-soft);
    white-space: nowrap;
  }
  .owner-name {
    position: absolute;
    left: 38px;
    top: 372px;
    font-family: "Great Vibes", cursive;
    font-size: 56px;
    line-height: 1.2;
    color: var(--ink);
    white-space: nowrap;
  }
  .social-handle {
    position: absolute;
    left: 38px;
    top: 490px;
    display: flex;
    align-items: center;
    gap: 14px;
    font-size: 25px;
    font-weight: 300;
    color: var(--contact-ink);
  }
  .social-dot {
    width: 22px; height: 22px; border-radius: 50%;
    background: var(--dot-pink);
  }
  .contact-list {
    position: absolute;
    left: 580px;
    top: 378px;
    list-style: none;
  }
  .contact-item {
    display: flex;
    align-items: center;
    gap: 16px;
    height: 39px;
    font-size: 25px;
    font-weight: 300;
    color: var(--contact-ink);
    white-space: nowrap;
  }
  .contact-icon { width: 20px; height: 20px; fill: var(--icon-ink); flex: none; }
  .bottom-strip { position: absolute; left: 0; bottom: 0; }
  .vat-number {
    position: absolute;
    left: 578px;
    top: 548px;
    font-size: 23px;
    font-weight: 300;
    color: var(--band-text);
    letter-spacing: 0.3px;
  }
</style>
</head>
<body>
  <div class="business-card">
    <div class="brand-name">Lunavita Chef</div>
    <div class="tagline">Leggera con i piatti del cuore</div>

    <div class="owner-name">Luna Ferrante</div>
    <div class="social-handle"><span class="social-dot"></span>@Lunavita27</div>

    <ul class="contact-list">
      <li class="contact-item">
        <svg class="contact-icon" viewBox="0 0 20 20"><path d="M2 6c0-2 3-3 8-3s8 1 8 3v2h-4V6.5c-1-.4-2.5-.5-4-.5s-3 .1-4 .5V8H2zM4 9h12l1 8H3z"/></svg>
        000-0000-0000
      </li>
      <li class="contact-item">
        <svg class="contact-icon" viewBox="0 0 20 20"><path d="M1 4h18v12H1zM3 6v.5l7 5 7-5V6z"/></svg>
        info@piattileggeriorto.it
      </li>
      <li class="contact-item">
        <svg class="contact-icon" viewBox="0 0 20 20"><circle cx="10" cy="10" r="8" fill="none" stroke="#8a9a94" stroke-width="1.6"/><path d="M2 10h16M10 2c-3 3-3 13 0 16M10 2c3 3 3 13 0 16" fill="none" stroke="#8a9a94" stroke-width="1.4"/></svg>
        www.piattileggeriorto.it
      </li>
    </ul>

    <svg class="bottom-strip" width="1000" height="90" viewBox="0 0 1000 90">
      <rect x="0" y="70" width="520" height="20" fill="var(--strip-teal)"/>
      <path d="M490 90 C520 60 530 18 570 18 H1000 V90 Z" fill="var(--band-dark)"/>
    </svg>
    <div class="vat-number">Partita IVA 01234560789</div>
  </div>
</body>
</html>
```